KRWB new business card design

We need a business card design for our established business which is Australia wide however based in Melbourne. We are a young team of Financial Planners who specialize in Insurance and Basic super advice for people like us.

We are people who help our clients get things done in a timely and cost effective manner whilst having a good time and a laugh along the way.

We would like this to have a consistent feel with our new e-brochure which i have attached from a color and font perspective.

Industry/Entity Type

Business

Requirements
Must have
• We do not need specific address details rather just the states we are in:

VIC/NSW/QLD/TAS
Nice to have
• Curved edge to mate the brochure

```html
<!DOCTYPE html>
<html lang="en">
<head>
<meta charset="utf-8">
<title>KRWB Business Card</title>
<link href="https://fonts.googleapis.com/css2?family=Arimo:wght@400;700&display=swap" rel="stylesheet">
<style>
  :root {
    --canvas: #e9e7e2;
    --card-dark: #2a2d2b;
    --card-deep: #26302a;
    --curve-shade: #2c3a2e;
    --lime: #8cc63f;
    --leaf: #4fa84e;
    --white: #ffffff;
    --soft-white: #e6ebe4;
  }
  * { margin: 0; padding: 0; box-sizing: border-box; }
  html, body { width: 1200px; height: 900px; overflow: hidden; }
  body {
    background: var(--canvas);
    font-family: "Arimo", Arial, sans-serif;
    position: relative;
  }
  .card {
    position: absolute;
    width: 560px;
    height: 320px;
    border-radius: 6px;
    overflow: hidden;
    background: var(--card-dark);
    box-shadow: 0 6px 18px rgba(0,0,0,0.18);
  }
  .card--front { left: 90px; top: 110px; }
  .card--back { left: 550px; top: 470px; background: linear-gradient(135deg, var(--card-dark) 0%, var(--card-deep) 100%); }
  .card__shapes { position: absolute; inset: 0; }

  .brand { position: absolute; display: flex; }
  .brand__mark { background: var(--lime); border-radius: 6px; flex: none; }
  .brand__name { color: var(--white); font-weight: 700; line-height: 1.05; }

  .card--front .brand { left: 52px; top: 92px; align-items: flex-start; gap: 16px; }
  .card--front .brand__mark { width: 112px; height: 112px; }
  .card--front .brand__name { font-size: 24px; margin-top: 12px; }

  .card--back .brand { left: 34px; top: 58px; flex-direction: column; gap: 10px; }
  .card--back .brand__mark { width: 64px; height: 64px; }
  .card--back .brand__name { font-size: 17px; }

  .tagline {
    position: absolute; left: 140px; top: 60px;
    color: var(--white); font-weight: 700; font-size: 21px; line-height: 1.2;
    letter-spacing: 0.3px;
  }
  .regions {
    position: absolute; right: 30px; top: 104px;
    list-style: none; text-align: right;
    color: var(--soft-white); font-size: 13px; line-height: 1.35; letter-spacing: 0.4px;
  }
  .contact {
    position: absolute; left: 34px; bottom: 26px;
    list-style: none; color: var(--soft-white); font-size: 13px; line-height: 1.4; letter-spacing: 0.3px;
  }
</style>
</head>
<body>

<section class="card card--front" aria-label="Card front">
  <svg class="card__shapes" width="560" height="320" viewBox="0 0 560 320" aria-hidden="true">
    <path d="M40 320 V250 Q40 200 90 200 H330 Q380 200 380 250 V320 Z" fill="var(--curve-shade)"/>
    <path d="M372 0 H560 V320 H420 Q396 320 396 296 V60 Q396 10 372 0 Z" fill="var(--leaf)"/>
    <path d="M384 0 H560 V320 H432 Q410 320 410 296 V60 Q410 12 384 0 Z" fill="var(--lime)"/>
  </svg>
  <div class="brand">
    <span class="brand__mark"></span>
    <span class="brand__name">Kelway Rise<br>Wealth</span>
  </div>
</section>

<section class="card card--back" aria-label="Card back">
  <svg class="card__shapes" width="560" height="320" viewBox="0 0 560 320" aria-hidden="true">
    <path d="M120 320 V190 Q120 140 170 140 H430 Q480 140 480 190 V320 H440 V200 Q440 180 420 180 H180 Q160 180 160 200 V320 Z" fill="var(--curve-shade)"/>
  </svg>
  <div class="brand">
    <span class="brand__mark"></span>
    <span class="brand__name">Kelway Rise<br>Wealth</span>
  </div>
  <p class="tagline">STEADY PLANS,<br>BRIGHTER LIVING</p>
  <ul class="regions">
    <li>TASMANIA</li>
    <li>VICTORIA</li>
    <li>GOLD COAST</li>
    <li>NEW SOUTH WALES</li>
  </ul>
  <ul class="contact">
    <li>1300 555 014</li>
    <li>admin@krwb.com.au</li>
    <li>www.kelwayrisewealth.com.au</li>
  </ul>
</section>

</body>
</html>
```